Shopping centre customer engagement software website

We need a multi page site with :

*What we do.
*How it works.
*Benefits
* Case study
* Testimonial
* Business login (we provide link to business portal)
* Consumer login (we provide link to consumer site)
* Book a demo
* Contact us

We want it to be clean and crisp and very self explanatory with little clutter. We are thinking white but are open to what ever looks the best.
Updates

Wordpress is preferred

Need extra days to review

Target Market(s)

Shopping centre managers and retail property companies

Coding

Coded - Design and coding required

Number of Pages Required

5+ page

Font styles to use
Sans Serif

Colors
ffffff

Requirements
Must have
• As listed above and must be responsive! Checkout our existing site for the text to be included (will be edited but it’ll give you an idea) www.vostrelink.com

```html
<!DOCTYPE html>
<html lang="en">
<head>
<meta charset="utf-8">
<title>Vostrelink – Shopping centre engagement</title>
<link href="https://fonts.googleapis.com/css2?family=Open+Sans:ital,wght@0,300;0,400;0,600;0,700;1,400&display=swap" rel="stylesheet">
<style>
:root{
  --accent:#6cc3dc;
  --accent-dark:#4fb0cc;
  --ink:#222;
  --text:#555;
  --muted:#888;
  --band:#f3f4f6;
  --line:#e3e5e8;
  --white:#fff;
}
*{box-sizing:border-box;margin:0;padding:0}
html,body{width:1200px;height:3130px;overflow:hidden}
body{font-family:"Open Sans",Arial,sans-serif;color:var(--text);background:var(--white);position:relative}
.abs{position:absolute}

/* hero */
.hero{position:absolute;left:0;top:0;width:1200px;height:545px;
  background:linear-gradient(180deg,#6f7f8c 0%,#a9b1b6 35%,#8d8a82 70%,#5b5650 100%)}
.hero::after{content:"";position:absolute;inset:0;background:rgba(20,30,40,.25)}
.topbar{position:absolute;left:0;top:0;width:1200px;height:70px;z-index:2}
.logo{position:absolute;display:flex;align-items:center;gap:12px;font-weight:600;letter-spacing:3px;font-size:24px;color:var(--white)}
.logo .dot{width:44px;height:44px;border-radius:50%;background:#cfd6db}
.nav{position:absolute;left:388px;top:26px;display:flex;gap:30px}
.nav a{color:var(--white);font-size:14px;font-weight:600;text-decoration:none}
.btn-login{position:absolute;top:17px;height:34px;border-radius:17px;font-size:14px;font-weight:600;display:flex;align-items:center;justify-content:center}
.btn-consumer{left:874px;width:140px;border:2px solid var(--white);color:var(--white)}
.btn-business{left:1023px;width:140px;background:var(--white);color:var(--ink)}
.hero-title{position:absolute;left:330px;top:226px;width:520px;text-align:center;color:var(--white);font-size:24px;font-weight:300;line-height:34px;z-index:2}

/* learn bar */
.learnbar{position:absolute;left:0;top:545px;width:1200px;height:31px;background:#ededed;font-size:12.5px;color:#8a8a8a}
.learnbar .links{position:absolute;left:52px;top:7px;display:flex;gap:20px}
.learnbar .social{position:absolute;left:1000px;top:7px;display:flex;gap:22px;align-items:center}
.sq{width:17px;height:17px;border-radius:2px}

/* what we do */
.h-what{position:absolute;left:52px;top:604px;font-size:33px;font-weight:700;color:var(--ink)}
.what-copy{position:absolute;left:52px;top:652px;width:600px;font-size:12.5px;line-height:19px}
.what-copy p+p{margin-top:20px}
.pill{position:absolute;top:852px;height:34px;border:2px solid #bfe4ef;border-radius:17px;color:var(--accent);font-size:13px;font-weight:700;display:flex;align-items:center;justify-content:center;gap:8px;letter-spacing:.5px}
.link-why{position:absolute;left:240px;top:861px;color:var(--accent);font-weight:700;font-size:13px;letter-spacing:.5px}
.screens{position:absolute;left:668px;top:626px;width:532px;height:236px;background:linear-gradient(90deg,#e9ecef,#f6f7f8 40%,#dcd6c8)}
.divider{position:absolute;left:52px;top:929px;width:1096px;height:1px;background:var(--line)}
.feature{position:absolute;top:982px;width:345px}
.feature h3{font-size:17px;color:var(--ink);font-weight:600;display:flex;align-items:center;gap:10px;margin-bottom:10px}
.feature p{font-size:12.5px;line-height:19px}

/* how it works */
.band{position:absolute;left:0;width:1200px;background:var(--band)}
.section-title{position:absolute;left:0;width:1200px;text-align:center;color:var(--accent);font-size:32px;font-weight:600}
.steps-line{position:absolute;top:1373px;left:150px;width:898px;height:2px;background:#cfe9f1}
.step{position:absolute;top:1322px;width:200px;text-align:center}
.step .ico{width:100px;height:100px;margin:0 auto;background:var(--band);display:flex;align-items:center;justify-content:center}
.step h4{margin-top:18px;font-size:18px;font-weight:700;color:var(--ink)}
.step p{margin-top:16px;font-size:12.5px;line-height:18px;padding:0 12px}

/* clients */
.quote{position:absolute;left:228px;top:1722px;width:750px;font-style:italic;font-size:12.8px;line-height:20px;color:#777}
.quote-mark{position:absolute;left:226px;top:1700px;font-size:70px;color:var(--accent);font-weight:700;line-height:1}
.client{position:absolute;width:345px;height:156px;border:1px solid var(--line);display:flex;align-items:center;justify-content:center;gap:12px;font-size:30px;font-weight:600;color:#9a9a9a}
.client .mk{width:22px;height:22px;background:#9a9a9a}
.client.person{background:var(--band);border-color:var(--band)}
.avatar{width:72px;height:72px;border-radius:50%;background:linear-gradient(135deg,#c9b8a6,#6b5a4c)}
.person-name{font-size:17px;font-weight:700;color:var(--ink)}
.person-role{font-size:13px;color:#666;margin-top:4px;font-weight:400}

/* case study */
.case-sub{position:absolute;left:0;top:2300px;width:1200px;text-align:center;font-size:17px;color:#666}
.stat{position:absolute;top:2375px;width:253px;height:188px;color:var(--white);text-align:center}
.stat .num{position:absolute;top:44px;width:100%;font-size:44px;font-weight:700}
.stat .lbl{position:absolute;top:114px;width:100%;font-size:17px;font-weight:700}

/* contact */
.col-title{position:absolute;top:2650px;font-size:17px;font-weight:700;color:var(--ink)}
.field{position:absolute;border:1px solid #ccc;border-radius:3px;font-size:12px;color:#999;padding:7px 10px}
.send{position:absolute;left:52px;top:2888px;width:138px;height:32px;border-radius:16px;background:var(--accent);color:var(--white);font-size:12.5px;font-weight:700;display:flex;align-items:center;justify-content:center}
.map{position:absolute;left:334px;top:2697px;width:532px;height:225px;background:linear-gradient(135deg,#a9d3e8,#e8ece6 45%,#a9d3e8)}
.contact-info{position:absolute;left:895px;top:2690px;width:260px;font-size:12.5px;line-height:20px;color:#777}
.contact-info p{margin-bottom:10px}
.follow{position:absolute;left:895px;top:2845px;font-size:17px;font-weight:700;color:var(--ink)}
.circles{position:absolute;left:895px;top:2891px;display:flex;gap:12px}
.circles span{width:26px;height:26px;border-radius:50%;background:var(--accent)}

/* footer */
.footer{position:absolute;left:0;top:2966px;width:1200px;height:164px;border-top:3px solid var(--accent)}
.foot-main{position:absolute;left:52px;top:46px;display:flex;gap:28px;align-items:center;font-size:13px;font-weight:700;color:var(--ink)}
.foot-sub{position:absolute;left:52px;top:90px;display:flex;gap:24px;font-size:11.5px;color:#555}
.foot-right{position:absolute;left:902px;top:90px;display:flex;gap:24px;font-size:11.5px;color:#555}
.foot-logo{left:972px;top:16px;color:#777;font-size:22px}
.foot-logo .dot{background:#aab2b8}
</style>
</head>
<body>

<header class="hero" role="img" aria-label="City skyline photograph of office towers"></header>
<div class="topbar">
  <div class="logo" style="left:52px;top:12px"><span class="dot"></span>VOSTRELINK</div>
  <nav class="nav"><a>HOW IT WORKS</a><a>BENEFITS</a><a>WHAT WE DO</a><a>CASE STUDY</a></nav>
  <div class="btn-login btn-consumer">Consumer login</div>
  <div class="btn-login btn-business">Business login</div>
</div>
<h1 class="hero-title">Delight your shoppers, impress your tenants and provide your landlords with accurate detailed data in real time</h1>

<div class="learnbar">
  <div class="links"><span>Learn More:</span><span>Our Company</span><span>Testimonials</span><span>Careers</span><span>Help &amp; Contact</span></div>
  <div class="social">
    <span class="sq" style="background:#3b5a98"></span>
    <span class="sq" style="background:#4da7de"></span>
    <span class="sq" style="background:#d34836"></span>
    <svg width="16" height="16" viewBox="0 0 16 16"><circle cx="6.5" cy="6.5" r="5" fill="none" stroke="#777" stroke-width="2"/><line x1="10" y1="10" x2="15" y2="15" stroke="#777" stroke-width="2"/></svg>
  </div>
</div>

<h2 class="h-what">What we do</h2>
<div class="what-copy">
  <p>Vostrelink provides shopping centre managers with an easy to use platform which enables them to delight their shoppers, impress their tenants, provide detailed data to their landlords and all accessible to them at the click of button.</p>
  <p>Vostrelink gives shopping centres real time tracking through smart ID's of individual customer journeys through their physical stores, enabling highly targeted, relevant and timely promotional and rewarding capabilities. Furthermore, through deep analytical data processing of the customer journey, centre managers will be able to more accurately and reliably predict shopping behaviours.</p>
</div>
<div class="pill" style="left:52px;width:150px"><svg width="10" height="12" viewBox="0 0 10 12"><path d="M0 0L10 6L0 12Z" fill="#6cc3dc"/></svg>BOOK A DEMO</div>
<div class="link-why">WHY VOSTRELINK &nbsp;›</div>
<div class="screens" role="img" aria-label="App screens on phone and desktop mockups"></div>
<div class="divider"></div>

<div class="feature" style="left:52px">
  <h3><svg width="16" height="14" viewBox="0 0 16 14"><path d="M1 7l5 5L15 2" fill="none" stroke="#6cc3dc" stroke-width="3"/></svg>Example Scenario</h3>
  <p>Vostrelink can predict more accurately and more reliably than ever before that on a cold wet Thursday next week: 35% of a retailers customers coming through their doors will be women aged between 30-35 looking to buy kids wear. When they arrive Vostrelink can identify them personally and send them messages based on where they are and their preferences.</p>
</div>
<div class="feature" style="left:428px">
  <h3><svg width="16" height="14" viewBox="0 0 16 14"><path d="M1 7l5 5L15 2" fill="none" stroke="#6cc3dc" stroke-width="3"/></svg>Huge Benefits Potential</h3>
  <p>The potential benefits that Vostrelink offer shopping centres are huge. Vostrelink can enhance consumers' experience and simultaneously gather discrete, detailed location data that can be used to map shopping habits and staff activity. This insight will support the development of innovative centre layouts and customer service methods maximising efficiency.</p>
</div>
<div class="feature" style="left:803px">
  <h3><svg width="16" height="14" viewBox="0 0 16 14"><path d="M1 7l5 5L15 2" fill="none" stroke="#6cc3dc" stroke-width="3"/></svg>Vostrelink offers Malls</h3>
  <p>Their tenants the ability to connect with motivated customers and deliver filtered offers and discounts based on location, preferences and loyalty. Text messages are sent through Vostrelink's ability to track our unique smart loyalty cards. More importantly you can now provide your tenants with undisputable R.O.I of marketing spend with a detailed breakdown of how effective their marketing messages</p>
</div>

<section class="band" style="top:1204px;height:396px"></section>
<h2 class="section-title" style="top:1238px">How it works</h2>
<div class="steps-line"></div>
<div class="step" style="left:50px">
  <div class="ico"><svg width="80" height="80" viewBox="0 0 80 80" fill="none" stroke="#6cc3dc" stroke-width="2.5"><rect x="14" y="26" width="50" height="34" rx="4"/><path d="M22 26l30-12 6 12"/><rect x="46" y="36" width="18" height="12"/><circle cx="20" cy="62" r="8"/><path d="M16 62l3 3 5-6"/></svg></div>
  <h4>Allocate Cards</h4><p>Nemo enim ipsam voluptatem quia voluptas sit aspernatur aut odit aut fugit</p>
</div>
<div class="step" style="left:276px">
  <div class="ico"><svg width="80" height="80" viewBox="0 0 80 80" fill="none" stroke="#6cc3dc" stroke-width="2.5"><path d="M10 34h60l-8 34H18z"/><path d="M26 34c0-18 28-18 28 0"/><path d="M24 44h32M22 54h36"/></svg></div>
  <h4>Direct Marketing</h4><p>Nemo enim ipsam voluptatem quia voluptas sit aspernatur aut odit aut fugit</p>
</div>
<div class="step" style="left:501px">
  <div class="ico"><svg width="80" height="80" viewBox="0 0 80 80" fill="none" stroke="#6cc3dc" stroke-width="2.5"><rect x="28" y="8" width="24" height="44" rx="3"/><path d="M22 40v22l10 12h18l6-18V44"/><circle cx="40" cy="46" r="2"/></svg></div>
  <h4>Rewarding Loyalty</h4><p>Nemo enim ipsam voluptatem quia voluptas sit aspernatur aut odit aut fugit</p>
</div>
<div class="step" style="left:726px">
  <div class="ico"><svg width="80" height="80" viewBox="0 0 80 80" fill="none" stroke="#6cc3dc" stroke-width="2.5"><path d="M10 40L40 12l30 20-30 28z"/><path d="M24 34h30"/><circle cx="54" cy="56" r="10"/><path d="M54 50v12M48 56h12"/></svg></div>
  <h4>Collect Data</h4><p>Nemo enim ipsam voluptatem quia voluptas sit aspernatur aut odit aut fugit</p>
</div>
<div class="step" style="left:948px">
  <div class="ico"><svg width="80" height="80" viewBox="0 0 80 80" fill="none" stroke="#6cc3dc" stroke-width="2.5"><path d="M64 40a24 24 0 1 1-8-18"/><path d="M58 10v14H44"/></svg></div>
  <h4>Data Analytics</h4><p>Nemo enim ipsam voluptatem quia voluptas sit aspernatur aut odit aut fugit</p>
</div>

<h2 class="section-title" style="top:1620px">Our Clients</h2>
<div class="quote-mark">“</div>
<p class="quote">&nbsp;&nbsp;&nbsp;&nbsp;&nbsp;&nbsp;&nbsp;&nbsp;&nbsp;&nbsp;Provident, similique sunt in culpa qui officia deserunt mollitia animi, id est laborum et dolorum fuga eiusm like temporalis. Et harum quidem rerum facilis est et expedita distinctio. Nam libero tempore, cum soluta nobis. At vero eos et samus et iusto odio qui blanditiis praesentium voluptatum deleniti atque corrupti quos jfont dolores et autem quibusdam et aut officis perferendis doloribus.</p>

<div class="client" style="left:52px;top:1828px"><span class="mk"></span>Novalta</div>
<div class="client" style="left:428px;top:1828px">Tandem Studio</div>
<div class="client" style="left:803px;top:1828px"><span class="mk" style="border-radius:50%"></span>Orbix</div>
<div class="client" style="left:52px;top:2014px"><span class="mk" style="border-radius:50%"></span>Lumora</div>
<div class="client person" style="left:428px;top:2014px">
  <span class="avatar" role="img" aria-label="Portrait of Clara Henley"></span>
  <div><div class="person-name">Clara Henley</div><div class="person-role">Creative Designer</div></div>
</div>
<div class="client" style="left:803px;top:2014px">Kestrel</div>

<section class="band" style="top:2212px;height:401px"></section>
<h2 class="section-title" style="top:2228px">Case study</h2>
<p class="case-sub">Results from a 31 day campaign</p>
<div class="stat" style="left:52px;background:linear-gradient(160deg,#5b5048,#2b2623)" role="img" aria-label="Photo of shoppers with cards"><div class="num">650</div><div class="lbl">VIP Card Holders</div></div>
<div class="stat" style="left:334px;background:linear-gradient(160deg,#6a5540,#2c231c)" role="img" aria-label="Photo of person reading messages"><div class="num">10500</div><div class="lbl">Messages Sent</div></div>
<div class="stat" style="left:616px;background:linear-gradient(160deg,#4f5a62,#252a2e)" role="img" aria-label="Photo of shoppers receiving rewards"><div class="num">980</div><div class="lbl">Loyalty Rewards Issued</div></div>
<div class="stat" style="left:898px;background:linear-gradient(160deg,#3a3434,#5a2a28)" role="img" aria-label="Photo of store tenant"><div class="num">95 %</div><div class="lbl">Tenant Engagement</div></div>

<h3 class="col-title" style="left:52px">Feel Free to Mail</h3>
<div class="field" style="left:52px;top:2697px;width:118px;height:31px">Name *</div>
<div class="field" style="left:188px;top:2697px;width:117px;height:31px">Email *</div>
<div class="field" style="left:52px;top:2747px;width:253px;height:31px">Subject</div>
<div class="field" style="left:52px;top:2799px;width:253px;height:72px">Write Your Message Here...</div>
<div class="send">SEND MESSAGE</div>

<h3 class="col-title" style="left:334px;width:532px;text-align:center;top:2655px">Headquarters</h3>
<div class="map" role="img" aria-label="Street map showing the headquarters location"></div>

<h3 class="col-title" style="left:895px">Contact Info</h3>
<div class="contact-info">
  <p>Our staff is available to you from 9AM until 5PM on weekdays.</p>
  <p>Phone: +44 (020) 014 77 31</p>
  <p>Office: Unit 7b, Harbour Row, BT90 2XY</p>
  <p>Email: dana@vostrelink.com</p>
</div>
<h3 class="follow">Follow Us on</h3>
<div class="circles"><span></span><span></span><span></span><span></span><span></span></div>

<footer class="footer">
  <div class="foot-main">
    <svg width="14" height="14" viewBox="0 0 16 16"><circle cx="6.5" cy="6.5" r="5" fill="none" stroke="#444" stroke-width="2"/><line x1="10" y1="10" x2="15" y2="15" stroke="#444" stroke-width="2"/></svg>
    <span>Help &amp; Contact</span><span>Benefits</span><span>Case Study</span><span>How it works</span>
  </div>
  <div class="logo foot-logo"><span class="dot"></span>VOSTRELINK</div>
  <div class="foot-sub"><span>About</span><span>Blog</span><span>Careers</span><span>Public Policy</span><span>What we do</span><span>Testimonials</span><span>Partners</span></div>
  <div class="foot-right"><span>© 2006 - 2018</span><span>Privacy</span><span>Legal</span><span>Feedback</span></div>
</footer>

</body>
</html>
```